Natural Light/Organic/Documentary Photography Business

I like a simple, approachable, feminine, earthy/organic feel. Earth/neutral tones, nothing too loud or obnoxious. I like the watercolor look. I don't want anything too trendy or something I'll get tired of after a couple months. As far as colors, I am much more a fan of cream/taupe/blue/green...not a fan of pink or purple at all.

Target Market(s)

Weddings & Families

Industry/Entity Type

Wedding Photography

Contact Information for Business Card

website, email, phone number

Font styles to use
Other font styles liked:
• Horizontes, Gotham

Colors

Designer to choose colors to be used in the design.

Requirements
Must have
• Website: www.mirelhatchway.com
• Phone: 418.629.5073
• Email: mirel@mirelhatchway.com
Nice to have
• I like the watercolor look but its not necessary. I like simple/earthy tones. Nothing too loud or distracting. Simple & feminine without being too girly. I like an approachable/soft feel.
• Instagram: www.instagram.com/mirelhatchwayphotography/
Should not have
• NO loud colors or design or pattern. I do not want a photo of a camera or lens or anything cheesy like that.

```html
<!DOCTYPE html>
<html lang="en">
<head>
<meta charset="utf-8">
<title>Mirel Hatchway Photography — Business Card</title>
<link rel="stylesheet" href="https://fonts.googleapis.com/css2?family=Source+Sans+3:wght@400;600&display=swap">
<style>
  :root {
    --backdrop: #ebebeb;
    --card: #ffffff;
    --taupe: #8c7f76;
    --ink: #3a3a3a;
    --ink-soft: #4a4a4a;
  }
  * { margin: 0; padding: 0; box-sizing: border-box; }
  html, body {
    width: 1200px; height: 799px; overflow: hidden;
    background: var(--backdrop);
    font-family: "Source Sans 3", "Myriad Pro", Arial, sans-serif;
  }
  .card {
    position: absolute;
    left: 313px; width: 584px; height: 333px;
    background: var(--card);
  }
  .card::before {
    content: ""; position: absolute; left: 0; top: 0; bottom: 0;
    width: 16px; background: var(--taupe);
  }
  .card--front { top: 51px; }
  .card--back { top: 412px; }

  .brand-corner {
    position: absolute; right: 44px; top: 40px;
    font-size: 14px; font-weight: 400; color: var(--taupe);
    letter-spacing: 0.04em;
  }
  .holder-name {
    position: absolute; left: 47px; top: 196px;
    font-size: 21px; font-weight: 600; color: var(--taupe);
  }
  .contact-list {
    position: absolute; left: 47px; top: 230px;
    list-style: none;
  }
  .contact-list li {
    display: flex; align-items: center;
    height: 19px;
    font-size: 15.5px; color: var(--ink);
  }
  .contact-icon {
    width: 13px; height: 13px; margin-right: 8px; flex: none;
    fill: var(--ink-soft);
  }

  .brand-lockup {
    position: absolute; left: 16px; right: 0; top: 132px;
    text-align: center; color: var(--taupe);
  }
  .brand-name {
    font-size: 38px; font-weight: 400; letter-spacing: 0.02em; line-height: 1;
  }
  .brand-tagline {
    margin-top: 10px;
    font-size: 9.5px; letter-spacing: 0.62em; padding-left: 0.62em;
  }
  .website-line {
    position: absolute; left: 16px; right: 0; top: 277px;
    text-align: center;
    font-size: 15px; letter-spacing: 0.26em; color: var(--ink-soft);
  }
</style>
</head>
<body>
  <section class="card card--front">
    <div class="brand-corner">Mirel Hatchway</div>
    <h1 class="holder-name">Mirel Hatchway</h1>
    <ul class="contact-list">
      <li>
        <svg class="contact-icon" viewBox="0 0 16 16" aria-hidden="true">
          <path d="M1 6c0-2 3-3.5 7-3.5S15 4 15 6v1.2h-3.4V5.6H4.4v1.6H1z"/>
          <path d="M3.5 8.2 5 6.5h6l1.5 1.7V14h-9z"/>
          <circle cx="8" cy="10.5" r="1.6" fill="#fff"/>
        </svg>418.629.5073
      </li>
      <li>
        <svg class="contact-icon" viewBox="0 0 16 16" aria-hidden="true">
          <path d="M1 3.5h14v1.2L8 9 1 4.7z"/>
          <path d="M1 6.2 8 10.5l7-4.3V13H1z"/>
        </svg>mirel@mirelhatchway.com
      </li>
      <li>
        <svg class="contact-icon" viewBox="0 0 16 16" aria-hidden="true">
          <circle cx="8" cy="8" r="7"/>
          <path d="M4 4.5c1.5 0 2 1 3 1.5s.5 2-1 2.2-1 2-.3 3.3M10 3c-.5 1.5.8 2 2 2.3M11 9c1 .5 1 2 .2 3" stroke="#fff" stroke-width="1.1" fill="none"/>
        </svg>www.mirelhatchway.com
      </li>
      <li>
        <svg class="contact-icon" viewBox="0 0 16 16" aria-hidden="true">
          <rect x="1.5" y="1.5" width="13" height="13" rx="2"/>
        </svg>mirelhatchwayphotography
      </li>
    </ul>
  </section>

  <section class="card card--back">
    <div class="brand-lockup">
      <div class="brand-name">Mirel Hatchway</div>
      <div class="brand-tagline">PHOTOGRAPHY</div>
    </div>
    <div class="website-line">WWW.MIRELHATCHWAY.COM</div>
  </section>
</body>
</html>
```